Graphic Design Project

ok I have the artwork for my presentation folder, and I have the text to put on the folder, I need you to apply text to the folder and the single sheets, so inside the artwork is pictures to use, text to use. thank you so much ask me as many questions as you need
Updates

my girl forgot to upload the mock ups of the presentation folder and single sheets, my apologies please check updated files

Hey Guys this is a eazy project the artwork is done, the text is done, the pictures are done!, all you have to do is assemble the project, I even have mock up pictures of how project looks finished, I have made the money good so that you would not pass on this project because it is not that creative of a job!

Target Market(s)

Dr's and patients

Industry/Entity Type

Graphic Design

Requirements
Must have
• use the single sheet artwork to make as many single sheets as you need to use all of the text supplied
Should not have
• do not make this, so professional looking that it does not appeal to the patients

```html
<!DOCTYPE html>
<html lang="en">
<head>
<meta charset="utf-8">
<title>KindPath Counseling – Presentation Folder Inside</title>
<link rel="stylesheet" href="https://fonts.googleapis.com/css2?family=Open+Sans:wght@400;600;700&display=swap">
<style>
  :root {
    --canvas: #e9e9e9;
    --paper: #ffffff;
    --brown: #8b5a32;
    --brown-dark: #4b2a16;
    --beige: #b8a78a;
    --beige-light: #d9ccb2;
    --gold: #c9b27a;
    --photo-young-a: #8fa88a;
    --photo-young-b: #c9a98a;
    --photo-couple-a: #b9ab98;
    --photo-couple-b: #7f9a84;
    --text: #4b2a16;
  }
  * { box-sizing: border-box; margin: 0; padding: 0; }
  html, body { width: 1200px; height: 1000px; overflow: hidden; }
  body {
    background: var(--canvas);
    font-family: "Open Sans", Arial, sans-serif;
    color: var(--text);
    position: relative;
  }
  .folder {
    position: absolute;
    left: 60px; top: 130px;
    width: 1080px; height: 720px;
    display: flex;
    box-shadow: 0 10px 30px rgba(0,0,0,0.18);
  }
  .panel {
    position: relative;
    width: 540px; height: 720px;
    background: var(--paper);
    overflow: hidden;
  }
  .panel + .panel { border-left: 1px solid #d6d6d6; }
  .panel-art { position: absolute; inset: 0; }

  .facts {
    position: absolute;
    left: 85px; top: 430px;
    width: 400px;
    list-style: none;
    font-size: 10px;
    line-height: 1.35;
    transform: rotate(-4deg);
    transform-origin: left top;
  }
  .facts li {
    position: relative;
    padding-left: 18px;
    margin-bottom: 11px;
  }
  .facts li::before {
    content: ">";
    position: absolute; left: 0; top: -3px;
    color: var(--paper);
    font-weight: 700;
    font-size: 17px;
  }
  .facts .lead { font-weight: 700; font-size: 14px; }

  .brand-mark {
    position: absolute;
    left: 16px; top: 350px;
    width: 92px; height: 92px;
    border-radius: 50%;
    background: radial-gradient(circle at 40% 35%, #f4efe4, var(--beige-light));
    border: 3px solid var(--paper);
  }

  .pocket-brand {
    position: absolute;
    left: 140px; top: 600px;
    display: flex; align-items: center; gap: 10px;
    color: var(--brown-dark);
    font-size: 26px; font-weight: 600;
    line-height: 1;
    white-space: nowrap;
  }
  .pocket-brand .dot {
    width: 14px; height: 14px; border-radius: 50%;
    background: var(--brown);
  }
</style>
</head>
<body>
<main class="folder">

  <section class="panel panel-left">
    <svg class="panel-art" viewBox="0 0 540 720" width="540" height="720">
      <defs>
        <linearGradient id="bandLeft" x1="0" y1="0" x2="1" y2="0">
          <stop offset="0" stop-color="#a9977a"/>
          <stop offset="0.55" stop-color="#c7b89c"/>
          <stop offset="1" stop-color="#a9977a"/>
        </linearGradient>
        <linearGradient id="youngPhoto" x1="0" y1="0" x2="1" y2="1">
          <stop offset="0" stop-color="var(--photo-young-a)"/>
          <stop offset="1" stop-color="var(--photo-young-b)"/>
        </linearGradient>
      </defs>
      <path class="band" d="M0 360 Q0 320 40 322 L540 395 V720 H0 Z" fill="url(#bandLeft)"/>
      <path class="photo" role="img" aria-label="Photo: four smiling young adults posing together outdoors under a tree"
            d="M0 0 H540 V320 Q540 352 508 348 L0 285 Z" fill="url(#youngPhoto)"/>
    </svg>
    <div class="brand-mark"></div>
    <ul class="facts">
      <li>"In 2011, at least <span class="lead">100 million Adult Americans</span> have chronic pain conditions"</li>
      <li>Nearly a million emergency department visits in 2011 were due to <span class="lead">People Misusing or Abusing Prescription</span> painkillers.</li>
      <li>where every patient is treated as a person with individual needs by professional, caring staff</li>
      <li>Many Pain Management Physicians are interested in reducing risk to their patients and practice from opiod misuse and Increasing Quality Care for their Patients!</li>
      <li><span class="lead">KindPath Counseling</span> is a resource for Pain Management Clinics to educate and provide prevention and counseling program to patients to reduce the risk of substance use disorders for those patients at risk to pain related substance use disorders.</li>
    </ul>
  </section>

  <section class="panel panel-right">
    <svg class="panel-art" viewBox="0 0 540 720" width="540" height="720">
      <defs>
        <linearGradient id="couplePhoto" x1="0" y1="0" x2="1" y2="1">
          <stop offset="0" stop-color="var(--photo-couple-a)"/>
          <stop offset="1" stop-color="var(--photo-couple-b)"/>
        </linearGradient>
        <linearGradient id="pocketFill" x1="0" y1="0" x2="1" y2="0">
          <stop offset="0" stop-color="#f3f1ec"/>
          <stop offset="0.6" stop-color="#e6dcc6"/>
          <stop offset="1" stop-color="var(--gold)"/>
        </linearGradient>
      </defs>
      <path class="tab" d="M110 0 H540 V95 Q540 125 510 115 L110 12 Z" fill="var(--brown)"/>
      <path class="pocket-back" d="M0 400 L540 520 V720 H0 Z" fill="var(--beige)"/>
      <path class="photo" role="img" aria-label="Photo: smiling older couple lying side by side on a rug"
            d="M40 6 L515 138 Q540 145 540 172 V560 L20 395 Q4 390 4 372 V40 Q4 0 40 6 Z" fill="url(#couplePhoto)"/>
      <path class="pocket-frame" d="M20 720 V470 Q20 440 52 446 L540 545 V720 Z" fill="var(--brown)"/>
      <path class="pocket-face" d="M40 720 V488 Q40 462 66 467 L510 558 V705 H40 Z" fill="url(#pocketFill)"/>
    </svg>
    <div class="pocket-brand"><span class="dot"></span>KindPath Counseling</div>
  </section>

</main>
</body>
</html>
```